Harborview Estates Business Card for Apartment Buildings

Create business cards for resident managers who run apartment buildings. The audience is the public who are searching for apartment rentals, and current residents who live at the apartment building. Key design element will be incorporating the company logo, however, the logo cannot dominate. The building name and manager name are more important than the logo. Current business card design leaves little room for copy, so we may need to reduce the size on the current card to allow for more space for copy.

Target Market(s)

Adults 18-65 years of age, who are looking for an apartment rental, plus current residents who live at our apartment buildings.

Industry/Entity Type

Property Management

Contact Information for Business Card

A major design element will be use of the company logo. Important property and manager contact information must be part of the design. The size of the logo will need to be reduced to make room for building and manager contact copy.

Font styles to use
Sans Serif

Colors
3176b5
000000
959595
ffffff

Requirements
Must have
• 1) Incorporate the company logo.
• 2) Use the company colors (dark blue, black/grey, over white).
• 3) FEATURE THE BUILDING NAME
• 4) FEATURE THE MANAGER NAME
• 5) The company name is less important than BUILDING and MANAGER
• 6) Manager contact information
• **SEE ATTACHED CREATIVE BRIEF**
Nice to have
• 1) Back of card logo watermark
• 2) Ability to write notes on back of carfd
Should not have
• Avoid letting the company logo dominate the card, the building name and manager are more important than the company logo.

```html
<!DOCTYPE html>
<html lang="en">
<head>
<meta charset="utf-8">
<title>Harborview Estates – Resident Manager Business Card</title>
<link rel="stylesheet" href="https://fonts.googleapis.com/css2?family=Roboto+Condensed:wght@400;700&family=Roboto:wght@400&display=swap">
<style>
  :root {
    --brand-blue: #0f65a3;
    --ink-dark: #444548;
    --ink-text: #4a4a4a;
    --grey-mid: #959595;
    --paper: #f3f3f3;
    --page-bg: #e4e4e4;
    --white: #ffffff;
    --watermark: #dcdcdc;
  }
  * { margin: 0; padding: 0; box-sizing: border-box; }
  html, body { width: 1200px; height: 960px; overflow: hidden; }
  body { background: var(--page-bg); position: relative; font-family: "Roboto", Arial, sans-serif; }

  .card {
    position: absolute;
    width: 600px;
    height: 342px;
    background: var(--paper);
    overflow: hidden;
    box-shadow: 0 2px 6px rgba(0,0,0,.18);
  }
  .card--front { left: 314px; top: 113px; }
  .card--back  { left: 311px; top: 472px; }

  .company-mark {
    position: absolute;
    left: 38px; top: 50px;
    display: flex; align-items: center; gap: 10px;
    font-family: "Roboto Condensed", Arial, sans-serif;
    font-weight: 700;
    font-size: 26px;
    color: var(--brand-blue);
    letter-spacing: .5px;
  }
  .company-mark__dot {
    width: 30px; height: 30px; border-radius: 50%;
    background: var(--brand-blue);
  }

  .property {
    position: absolute;
    right: 40px; top: 122px;
    text-align: right;
  }
  .property__name {
    font-family: "Roboto Condensed", Arial, sans-serif;
    font-weight: 700;
    font-size: 22px;
    color: var(--brand-blue);
    line-height: 1;
    margin-bottom: 5px;
  }
  .property__address {
    font-size: 14.5px;
    color: var(--ink-text);
    line-height: 18px;
  }

  .contact-list {
    position: absolute;
    right: 40px; top: 189px;
    list-style: none;
    text-align: right;
  }
  .contact-list li {
    display: flex; justify-content: flex-end; align-items: center; gap: 7px;
    font-size: 14.5px;
    color: var(--ink-text);
    height: 19.3px;
  }
  .contact-list svg { width: 14px; height: 14px; fill: var(--brand-blue); }

  .footer-bands { position: absolute; left: 0; top: 270px; width: 600px; height: 72px; }

  .manager {
    position: absolute;
    left: 38px; top: 282px;
    color: var(--white);
    font-family: "Roboto Condensed", Arial, sans-serif;
  }
  .manager__name { font-weight: 700; font-size: 23px; line-height: 1.1; }
  .manager__title { font-size: 16px; line-height: 1.3; }

  .back-mark {
    position: absolute;
    inset: 0;
    display: flex; align-items: center; justify-content: center;
    font-family: "Roboto Condensed", Arial, sans-serif;
    font-weight: 700;
    font-size: 48px;
    letter-spacing: 1px;
    color: var(--watermark);
  }
</style>
</head>
<body>

<section class="card card--front" aria-label="Business card front">
  <div class="company-mark">
    <span class="company-mark__dot"></span>
    <span class="company-mark__name">HARBORVIEW ESTATES</span>
  </div>

  <div class="property">
    <p class="property__name">Cedar Crest Apartments</p>
    <p class="property__address">1482 Linden Avenue<br>Fairview, CA 94017</p>
  </div>

  <ul class="contact-list">
    <li>555-210-4837
      <svg viewBox="0 0 24 24"><path d="M6.6 10.8a15 15 0 0 0 6.6 6.6l2.2-2.2a1 1 0 0 1 1-.25 11.4 11.4 0 0 0 3.6.57 1 1 0 0 1 1 1V20a1 1 0 0 1-1 1A17 17 0 0 1 3 4a1 1 0 0 1 1-1h3.5a1 1 0 0 1 1 1c0 1.25.2 2.45.57 3.57a1 1 0 0 1-.25 1z"/></svg>
    </li>
    <li>555-318-6629
      <svg viewBox="0 0 24 24"><path d="M7 1h10a2 2 0 0 1 2 2v18a2 2 0 0 1-2 2H7a2 2 0 0 1-2-2V3a2 2 0 0 1 2-2zm0 3v14h10V4zm5 15.5a1 1 0 1 0 0 2 1 1 0 0 0 0-2z"/></svg>
    </li>
    <li>555-402-7150
      <svg viewBox="0 0 24 24"><path d="M6 2h12v5H6zM3 8h18a2 2 0 0 1 2 2v7h-4v5H5v-5H1v-7a2 2 0 0 1 2-2zm4 8v4h10v-4z"/></svg>
    </li>
    <li>marisol@harborviewest.com
      <svg viewBox="0 0 24 24"><path d="M2 4h20v16H2zm2 2v.5l8 5.5 8-5.5V6zm0 3v9h16V9l-8 5.5z"/></svg>
    </li>
    <li>www.harborviewest.com
      <svg viewBox="0 0 24 24"><circle cx="12" cy="12" r="10"/><path d="M8 7c2 0 3 1 2 3s-3 1-3 3 2 2 2 4" stroke="#fff" stroke-width="1.6" fill="none"/><path d="M15 6c-1 2 1 3 2 3M14 18c0-2 2-3 3-2" stroke="#fff" stroke-width="1.6" fill="none"/></svg>
    </li>
  </ul>

  <svg class="footer-bands" viewBox="0 0 600 72" preserveAspectRatio="none" aria-hidden="true">
    <polygon points="0,0 236,0 290,57 600,57 600,72 0,72" fill="var(--ink-dark)"/>
    <polygon points="269,30 600,30 600,54 292,54" fill="var(--white)"/>
    <polygon points="269,30 600,30 600,56 294,56" fill="var(--brand-blue)"/>
    <polygon points="236,0 240,0 292,54 288,57 290,57" fill="var(--white)"/>
  </svg>

  <div class="manager">
    <p class="manager__name">Marisol Delgado</p>
    <p class="manager__title">Resident Manager</p>
  </div>
</section>

<section class="card card--back" aria-label="Business card back">
  <p class="back-mark">HARBORVIEW ESTATES</p>
</section>

</body>
</html>
```